The most modern business card ever !!!

Our company call “Vendalo”. Vendalo is a technology company specialized in cruises solutions. Out main product is a platform to reserve cruises. This is a revolutionary platform that make easier to travel agencies and final users to reserve cruises across dozen companies like tibba, wernu, hpv, dgb, etc..We are a “start up”, with a young team of developers and we want to transmit it.. For it, we want something different, a modern business card that represent cruises and technology.. When someone receive this card, this person should say: wowww this is different… this is modern… this is a cruise related company..
- diferent, modern
- traditions business card

```html
<!DOCTYPE html>
<html lang="en">
<head>
<meta charset="utf-8">
<title>Vendalo business card</title>
<link href="https://fonts.googleapis.com/css2?family=Oswald:wght@500&family=Work+Sans:wght@400;600&display=swap" rel="stylesheet">
<style>
  :root {
    --stage: #161616;
    --card: #232323;
    --card-edge: #2c2c2c;
    --accent: #29a9e1;
    --ink: #ffffff;
    --ink-soft: #e6e6e6;
  }
  * { box-sizing: border-box; margin: 0; padding: 0; }
  html, body { width: 1200px; height: 900px; overflow: hidden; }
  body {
    background: radial-gradient(circle at 60% 40%, #2a2a2a 0%, var(--stage) 70%);
    font-family: "Work Sans", sans-serif;
    position: relative;
  }
  .card {
    position: absolute;
    left: 300px;
    width: 600px;
    height: 343px;
    background: linear-gradient(135deg, var(--card) 0%, var(--card-edge) 60%, var(--card) 100%);
    border-bottom: 5px solid var(--accent);
    box-shadow: 0 18px 40px rgba(0,0,0,.55);
    overflow: hidden;
  }
  .card--front { top: 88px; }
  .card--back { top: 467px; }

  .brand {
    position: absolute;
    inset: 0;
    display: flex;
    align-items: center;
    justify-content: center;
    gap: 18px;
  }
  .brand__mark {
    width: 22px; height: 22px;
    background: var(--accent);
  }
  .brand__name {
    font-weight: 600;
    font-size: 78px;
    letter-spacing: 2px;
    color: var(--ink);
  }

  .identity {
    position: absolute;
    top: 122px;
    left: 70px;
    width: 220px;
    text-align: right;
  }
  .identity__name {
    font-family: "Oswald", sans-serif;
    font-weight: 500;
    font-size: 33px;
    line-height: 1;
    letter-spacing: 1px;
    color: var(--accent);
    text-transform: uppercase;
  }
  .identity__role {
    margin-top: 8px;
    font-size: 15px;
    letter-spacing: 1.5px;
    color: var(--ink-soft);
  }
  .divider {
    position: absolute;
    top: 120px;
    left: 312px;
    width: 2px;
    height: 72px;
    background: var(--accent);
  }
  .contacts {
    position: absolute;
    top: 124px;
    left: 334px;
    list-style: none;
  }
  .contacts__item {
    display: flex;
    align-items: center;
    gap: 10px;
    font-size: 15px;
    letter-spacing: 1.3px;
    line-height: 22px;
    color: var(--ink-soft);
  }
  .contacts__icon { width: 11px; height: 11px; flex: none; }
  .address {
    position: absolute;
    left: 70px;
    bottom: 26px;
    font-size: 15px;
    letter-spacing: 1.5px;
    color: var(--ink-soft);
  }
</style>
</head>
<body>
  <section class="card card--front" aria-label="Card front">
    <div class="brand">
      <span class="brand__mark"></span>
      <span class="brand__name">Vendalo</span>
    </div>
  </section>

  <section class="card card--back" aria-label="Card back">
    <div class="identity">
      <p class="identity__name">Daniel Rourke</p>
      <p class="identity__role">Director</p>
    </div>
    <div class="divider"></div>
    <ul class="contacts">
      <li class="contacts__item">
        <svg class="contacts__icon" viewBox="0 0 12 12" fill="none" stroke="#29a9e1" stroke-width="1.6"><path d="M2 1.5h2.5l1 2.5-1.5 1a6 6 0 0 0 3 3l1-1.5 2.5 1v2.5A1 1 0 0 1 9.5 11 8.5 8.5 0 0 1 1 2.5a1 1 0 0 1 1-1z"/></svg>
        (514) 555-0172
      </li>
      <li class="contacts__item">
        <svg class="contacts__icon" viewBox="0 0 12 12" fill="none" stroke="#29a9e1" stroke-width="1.4"><rect x="1" y="2.5" width="10" height="7"/><path d="M1 2.5l5 4 5-4"/></svg>
        info@vendalo.com.br
      </li>
      <li class="contacts__item">
        <svg class="contacts__icon" viewBox="0 0 12 12" fill="none" stroke="#29a9e1" stroke-width="1.2"><circle cx="6" cy="6" r="5"/><ellipse cx="6" cy="6" rx="2.2" ry="5"/><path d="M1 6h10"/></svg>
        www.vendalo.com.br
      </li>
    </ul>
    <p class="address">214b Harlow Street, Brightmoor, NZ, 8042</p>
  </section>
</body>
</html>
```